Web site for a company that sells Pinball machines

We need a website that is an online shopping experience for a Store that sells pinball machines and accessories. The name of the store is called "Gadget Arcade." The store it self has a showroom, but we would also like to have an Internet e-commerce presence. We pinball machines made by Vexler pinball. You can visit their website and see their current list of machines as well as their website for the machines that we are going to carry in our store. Their website is Vexlerpinball.com. I am able to use their machine photos as well as their machine brochure PDF files. I am also able to use their logo on my website two list it as a Vexler Authorized Dealer.
This website design needs to be funky, fun, very technologically oriented and modern. The people buying machines our spending anywhere between $5000 and $15,000 on one machine. These Are high-end buyers who are also usually fairly tech savvy or at least enjoy technology and graphics.
Attachments: I have attached photographs of some of my own machines which may be used in the website. I've also attached some downloaded files from Vexler pinball.com as well as some of their PDF files for brochures. I will carry all of their current models they have listed under games. Not the archived games. I have included one of their machines called Thunderwolf Limited edition in my photograph attachments. The rest of the photos are just random pictures that I have taken myself and maybe used to build the site. Lastly I have attached my logo which I am not super crazy about so I will also be posting a contest to redesign this logo. Tons more of my own pinball photos are available.
I would like for people to be able to purchase machines and accessories from the website, but also inform them to our actual showroom.
Updates
Project Deadline Extended Reason: Hello. We have extended five days due to some complications during the construction of our actual building. We were unable to participate in this web design during this time and so unfortunately were not able give feedback appropriately. We are back on track and will provide feedback to the designers who have designed up until this point. We will still be interested in seeing new submissions, however; this extension will give us a chance to provide feedback and coordinate the website appropriately. Thank you so much for your submissions and your patience!!!!Gadget Arcade Added Friday, April 21, 2017
Target Market(s)
Target market is 16 to 75. Techy individuals to enjoy gaming technology video animation and Vegas style twinkle
Industry/Entity Type
It Company
Coding
Coded - Design and coding required
Number of Pages Required
3 page
Font styles to use
Look and feel
Each slider illustrates characteristics of the customer's brand and the style your logo design should communicate.

```html
<!DOCTYPE html>
<html lang="en">
<head>
<meta charset="utf-8">
<title>Gadget Arcade</title>
<link href="https://fonts.googleapis.com/css2?family=Poppins:wght@300;400;500;600;700&family=Open+Sans:wght@400;600&display=swap" rel="stylesheet">
<style>
:root{
  --dark:#333333;
  --ink:#111111;
  --white:#ffffff;
  --muted:#a9a9a9;
  --body:#555555;
  --card-left:#e6e6e6;
  --card-right:#efefef;
  --field-line:#6a6a6a;
  --nav:#555555;
  --fb:#3b5a9a;
  --tw:#1da1f2;
}
*{margin:0;padding:0;box-sizing:border-box}
html,body{width:1200px;height:2459px;overflow:hidden}
body{position:relative;font-family:"Open Sans",Arial,sans-serif;background:var(--white);color:var(--ink)}
section,header,footer{position:absolute;left:0;width:1200px}
.abs{position:absolute}

/* header */
.site-header{top:0;height:82px;background:linear-gradient(#fafafa,#ebebeb);z-index:3;box-shadow:0 4px 12px rgba(0,0,0,.25)}
.nav-link{position:absolute;top:31px;font-family:"Poppins",sans-serif;font-size:14px;font-weight:300;color:var(--nav);letter-spacing:.3px}
.nav-link.active{color:var(--ink);border-bottom:1px solid var(--ink);padding-bottom:1px}
.search{position:absolute;left:946px;top:31px;width:122px;border-bottom:1px solid #999;font-family:"Poppins",sans-serif;font-size:14px;font-weight:300;color:var(--nav);padding-bottom:3px}
.search svg{position:absolute;right:4px;top:3px}
.brand{position:absolute;left:500px;top:18px;width:200px;text-align:center;display:flex;align-items:center;justify-content:center;gap:8px;font-family:"Poppins",sans-serif;font-weight:700;font-size:20px;color:var(--dark)}
.brand-dot{width:12px;height:12px;border-radius:50%;background:var(--dark)}

/* hero */
.hero{top:82px;height:531px;background:radial-gradient(circle at 75% 55%,#8a8fa0 0,#4a4d5c 18%,transparent 40%),linear-gradient(120deg,#6a2c5e 0%,#2b2f4a 30%,#8c6a2a 55%,#3b2c4a 75%,#6b3046 100%)}
.hero-title{position:absolute;top:158px;left:0;width:1200px;text-align:center;font-family:"Poppins",sans-serif;font-weight:600;font-size:30px;line-height:38px;color:var(--white);text-shadow:0 2px 6px rgba(0,0,0,.5)}
.hero-arrow{position:absolute;top:255px;width:22px;height:22px;background:rgba(0,0,0,.45);display:flex;align-items:center;justify-content:center}

/* about */
.about{top:613px;height:264px;background:var(--dark);text-align:center}
.section-title{font-family:"Poppins",sans-serif;font-weight:600;font-size:32px;color:var(--white);letter-spacing:.3px}
.about .section-title{margin-top:75px}
.lead{width:940px;margin:10px auto 0;font-size:13px;line-height:23px;color:var(--muted)}

/* games */
.games{top:877px;height:480px;background:linear-gradient(110deg,#3a2a22 0%,#7a4a22 25%,#4a3020 45%,#8a3a2a 65%,#3a2a3a 85%,#6a4020 100%);text-align:center}
.games .section-title{margin-top:72px}
.product-card{position:absolute;left:131px;top:128px;width:935px;height:270px;display:flex;text-align:left}
.product-main{width:467px;background:var(--card-left);position:relative}
.product-info{flex:1;background:var(--card-right);padding:23px 36px 0 35px}
.machine-photo{position:absolute;left:38px;top:11px;width:129px;height:238px;background:linear-gradient(#4a3a6a,#6b4f8f 50%,#2a2440);border-radius:3px}
.product-name{position:absolute;left:257px;top:24px;font-family:"Poppins",sans-serif;font-weight:600;font-size:30px;color:var(--ink)}
.spec-label{position:absolute;left:257px;font-family:"Poppins",sans-serif;font-size:16px;color:var(--dark)}
.spec-dims{position:absolute;left:257px;font-family:"Poppins",sans-serif;font-size:12px;color:var(--dark);word-spacing:6px}
.order-btn{position:absolute;left:257px;top:206px;width:128px;height:38px;background:var(--ink);color:var(--white);font-family:"Poppins",sans-serif;font-size:15px;display:flex;align-items:center;justify-content:center}
.info-heading{font-family:"Poppins",sans-serif;font-size:15px;line-height:22px;color:var(--ink)}
.info-text{margin-top:14px;font-family:"Poppins",sans-serif;font-size:10px;line-height:18px;color:var(--body)}
.read-more{display:inline-block;margin-top:14px;font-family:"Poppins",sans-serif;font-size:10px;color:var(--ink);border-bottom:1px solid var(--ink)}

/* features */
.features{top:1357px;height:613px;background:linear-gradient(100deg,#e8d8d8 0%,#c9a0a0 20%,#b04040 38%,#d8c8c8 55%,#c25050 75%,#e4d4d4 100%)}
.feature-card{position:absolute;top:80px;width:216px;height:453px;background:var(--white);text-align:center;padding:40px 20px 0}
.feature-card svg{display:block;margin:0 auto}
.feature-title{margin-top:14px;font-family:"Poppins",sans-serif;font-weight:600;font-size:21px;line-height:24px;color:var(--ink);text-transform:uppercase}
.feature-text{margin-top:20px;text-align:left;font-family:"Poppins",sans-serif;font-size:10px;line-height:19px;color:var(--body)}

/* support */
.support{top:1970px;height:354px;background:var(--dark);text-align:center}
.support .section-title{margin-top:60px}
.support .lead{margin-top:8px}
.field{position:absolute;height:41px;border:1px solid var(--field-line);font-size:10px;color:#bbbbbb;text-align:left;padding:13px 14px}
.field svg{position:absolute;right:14px;top:16px}
.submit-btn{position:absolute;left:562px;top:297px;width:74px;height:39px;background:linear-gradient(#666,#3e3e3e);color:var(--white);font-family:"Poppins",sans-serif;font-size:12px;font-weight:500;display:flex;align-items:center;justify-content:center}

/* footer */
.site-footer{top:2324px;height:135px;background:var(--white)}
.footer-links{position:absolute;left:131px;top:67px;font-family:"Poppins",sans-serif;font-size:12px;color:var(--dark)}
.footer-links span{margin:0 9px;color:#888}
.copyright{position:absolute;left:131px;top:97px;font-family:"Poppins",sans-serif;font-size:12px;color:var(--dark)}
.social{position:absolute;top:76px;width:26px;height:26px;border-radius:50%}
</style>
</head>
<body>

<header class="site-header">
  <span class="nav-link active" style="left:131px">HOME</span>
  <span class="nav-link" style="left:215px">ABOUT</span>
  <span class="nav-link" style="left:306px">GAMES</span>
  <span class="nav-link" style="left:398px">BUY</span>
  <div class="brand"><span class="brand-dot"></span>Gadget Arcade</div>
  <span class="nav-link" style="left:710px">SUPPORT</span>
  <span class="nav-link" style="left:815px">COMMUNITY</span>
  <div class="search">SEARCH
    <svg width="13" height="13" viewBox="0 0 13 13"><circle cx="5.5" cy="5.5" r="4" fill="none" stroke="#111" stroke-width="2"/><line x1="8.5" y1="8.5" x2="12" y2="12" stroke="#111" stroke-width="2"/></svg>
  </div>
</header>

<section class="hero" role="img" aria-label="Close-up photograph of a lit pinball machine playfield with a chrome ball">
  <h1 class="hero-title">PELLENTESQUE HABITANT MORBI TRISTIQUE<br>SENECTUS ET NETUS ET MALESUADA</h1>
  <div class="hero-arrow" style="left:0"><svg width="10" height="10" viewBox="0 0 10 10"><path d="M6 1 2 5l4 4" fill="none" stroke="#fff" stroke-width="2"/></svg></div>
  <div class="hero-arrow" style="right:0"><svg width="10" height="10" viewBox="0 0 10 10"><path d="M4 1l4 4-4 4" fill="none" stroke="#fff" stroke-width="2"/></svg></div>
</section>

<section class="about">
  <h2 class="section-title">ABOUT GADGET ARCADE</h2>
  <p class="lead">Donec aliquam augue in quam tempor, quis sollicitudin magna posuere. Quisque ut nisi dapibus, commodo dui eget, pulvinar orci. Vestibulum est erat, eleifend in scelerisque ut, elementum id massa. Pellentesque luctus tellus in nisl aliquam, nec gravida neque placerat. Fusce molestie nulla nec enim varius aliquet. Fusce sit amet egestas erat, quis blandit libero. Integer malesuada erat quis tellus varius ultrices.</p>
</section>

<section class="games" role="img" aria-label="Blurred photograph of a colourful pinball playfield">
  <h2 class="section-title">GAMES</h2>
  <div class="product-card">
    <div class="product-main">
      <div class="machine-photo" role="img" aria-label="Photograph of a pinball cabinet with purple artwork"></div>
      <div class="product-name">PINBALL</div>
      <div class="spec-label" style="top:80px">BOXED :</div>
      <div class="spec-dims" style="top:104px">H:56” W:31” D:31” 280LBS</div>
      <div class="spec-label" style="top:146px">UNBOXED :</div>
      <div class="spec-dims" style="top:170px">H:75.5” W:27” D:55” 250LBS</div>
      <div class="order-btn">ORDER NOW</div>
    </div>
    <div class="product-info">
      <p class="info-heading">The people buying machines our spending anywhere between $5000 and $15,000 on one machine.</p>
      <p class="info-text">Integer nec enim vehicula, posuere ipsum ut, dapibus est. Morbi gravida ipsum nibh, ac tempor justo vulputate eget. Curabitur quis ex eget erat pulvinar placerat quis id libero. Pellentesque habitant morbi tristique senectus et netus et malesuada fames ac turpis egestas. Cras ultricies in quam efficitur commodo. Donec nec velit velit. Curabitur rhoncus facilisis augue ac tempor. In sollicitudin lobortis nulla et iaculis. Vivamus elit purus, bibendum eu sagittis vel, egestas eu ante. Phasellus convallis tristique magna vitae pulvinar.</p>
      <span class="read-more">READ MORE</span>
    </div>
  </div>
</section>

<section class="features" role="img" aria-label="Softly blurred photograph of red and white pinball cabinets">
  <article class="feature-card" style="left:131px">
    <svg width="34" height="32" viewBox="0 0 24 23"><path d="M12 1l3.2 7 7.3.6-5.5 4.8 1.7 7.4L12 17l-6.7 3.8L7 13.4 1.5 8.6 8.8 8z" fill="#111"/></svg>
    <h3 class="feature-title">Main<br>Attractions</h3>
    <p class="feature-text">Integer nec enim vehicula, posuere ipsum ut, dapibus est. Morbi gravida ipsum nibh, ac tempor justo vulputate eget. Curabitur quis ex eget erat pulvinar placerat quis id libero. Pellentesque habitant morbi tristique senectus et netus et malesuada fames ac turpis egestas. Cras ultricies in quam efficitur commodo. Donec nec velit velit. Curabitur rhoncus facilisis augue ac tempor. In sollicitudin lobortis nulla et iaculis. Vivamus elit purus, bibendum eu sagittis vel, egestas eu.</p>
  </article>
  <article class="feature-card" style="left:372px">
    <svg width="34" height="32" viewBox="0 0 24 23"><path d="M6 2h12v6a6 6 0 0 1-12 0z" fill="#111"/><path d="M6 4H2v2a4 4 0 0 0 4 4M18 4h4v2a4 4 0 0 1-4 4" fill="none" stroke="#111" stroke-width="2"/><rect x="10.5" y="13" width="3" height="5" fill="#111"/><rect x="7" y="18" width="10" height="3" fill="#111"/></svg>
    <h3 class="feature-title">Special Game<br>Features</h3>
    <p class="feature-text">Integer nec enim vehicula, posuere ipsum ut, dapibus est. Morbi gravida ipsum nibh, ac tempor justo vulputate eget. Curabitur quis ex eget erat pulvinar placerat quis id libero. Pellentesque habitant morbi tristique senectus et netus et malesuada fames ac turpis egestas. Cras ultricies in quam efficitur commodo. Donec nec velit velit. Curabitur rhoncus facilisis augue ac tempor. In sollicitudin lobortis nulla et iaculis. Vivamus elit purus, bibendum eu sagittis vel, egestas eu.</p>
  </article>
  <article class="feature-card" style="left:610px">
    <svg width="34" height="32" viewBox="0 0 24 22"><path d="M12 21 2.5 11.5A5.5 5.5 0 0 1 12 4a5.5 5.5 0 0 1 9.5 7.5z" fill="#111"/></svg>
    <h3 class="feature-title">Ramps and<br>Toys</h3>
    <p class="feature-text">Integer nec enim vehicula, posuere ipsum ut, dapibus est. Morbi gravida ipsum nibh, ac tempor justo vulputate eget. Curabitur quis ex eget erat pulvinar placerat quis id libero. Pellentesque habitant morbi tristique senectus et netus et malesuada fames ac turpis egestas. Cras ultricies in quam efficitur commodo. Donec nec velit velit. Curabitur rhoncus facilisis augue ac tempor. In sollicitudin lobortis nulla et iaculis. Vivamus elit purus, bibendum eu sagittis vel, egestas eu.</p>
  </article>
  <article class="feature-card" style="left:849px">
    <svg width="34" height="32" viewBox="0 0 24 23"><circle cx="9" cy="13" r="6" fill="none" stroke="#111" stroke-width="4" stroke-dasharray="3 2"/><circle cx="9" cy="13" r="2" fill="#111"/><circle cx="18" cy="5" r="3.5" fill="none" stroke="#111" stroke-width="3" stroke-dasharray="2 1.5"/><circle cx="19" cy="18" r="3" fill="none" stroke="#111" stroke-width="2.5" stroke-dasharray="2 1.5"/></svg>
    <h3 class="feature-title">Additional<br>Features</h3>
    <p class="feature-text">Integer nec enim vehicula, posuere ipsum ut, dapibus est. Morbi gravida ipsum nibh, ac tempor justo vulputate eget. Curabitur quis ex eget erat pulvinar placerat quis id libero. Pellentesque habitant morbi tristique senectus et netus et malesuada fames ac turpis egestas. Cras ultricies in quam efficitur commodo. Donec nec velit velit. Curabitur rhoncus facilisis augue ac tempor. In sollicitudin lobortis nulla et iaculis. Vivamus elit purus, bibendum eu sagittis vel, egestas eu.</p>
  </article>
</section>

<section class="support">
  <h2 class="section-title">SUPPORT</h2>
  <p class="lead">Pellentesque luctus tellus in nisl aliquam, nec gravida neque placerat. Fusce molestie nulla nec enim varius aliquet. Fusce sit amet egestas erat, quis blandit libero. Integer malesuada erat quis tellus varius ultrices.</p>
  <div class="field" style="left:131px;top:171px;width:218px">Name</div>
  <div class="field" style="left:370px;top:171px;width:219px">Email</div>
  <div class="field" style="left:608px;top:171px;width:219px">Phone</div>
  <div class="field" style="left:847px;top:171px;width:219px">Support For
    <svg width="8" height="5" viewBox="0 0 8 5"><path d="M1 1l3 3 3-3" fill="none" stroke="#bbb"/></svg>
  </div>
  <div class="field" style="left:131px;top:235px;width:935px">Message</div>
  <div class="submit-btn">SUBMIT</div>
</section>

<footer class="site-footer">
  <nav class="footer-links">Home<span>|</span>About<span>|</span>Games<span>|</span>Buy<span>|</span>Support<span>|</span>Community</nav>
  <p class="copyright">Copyright &copy; 2017 &nbsp;Company name. &nbsp;All rights reserved.</p>
  <span class="social" style="left:1008px;background:var(--fb)"></span>
  <span class="social" style="left:1040px;background:var(--tw)"></span>
</footer>

</body>
</html>
```